A start up Private Wine Label for export to Asia.

We are looking for the best graphic design for our very first wine label Corvessa Wines and would like the following requirements:

1. Black background - explore and play around the shade of black
2. Gold Shimmery Colour Font
3. Font should be a cursive classic posh that says Corvessa Wines
4. We would like the front graphic design to be simple and elegant and has a traditional classic feel to it.

Target Market(s)

Small scale to test the upper class market for export to Asia

Font styles to use
Script

Colors

Designer to choose colors to be used in the design.

Requirements
Must have
• Gold font for the label Corvessa Wines with shimmery touch to it.
• Elegant black background.
• Simple but elegant design.
• Attractive to the upper class market in Asia.
Nice to have
• Explore and play around with your imagination.

```html
<!DOCTYPE html>
<html lang="en">
<head>
<meta charset="UTF-8">
<title>Corvessa Wines – Label</title>
<link rel="stylesheet" href="https://fonts.googleapis.com/css2?family=Great+Vibes&display=swap">
<style>
  :root {
    --canvas: #ffffff;
    --label-black: #020202;
    --panel-center: #1b1b1b;
    --panel-edge: #070707;
    --pattern-gold: #4a3720;
    --pattern-dark: #0a0806;
    --gold: #d9b247;
  }
  html, body {
    margin: 0;
    padding: 0;
    width: 1200px;
    height: 1200px;
    overflow: hidden;
    background: var(--canvas);
  }
  .canvas {
    position: relative;
    width: 1200px;
    height: 1200px;
    background: var(--canvas);
  }
  .label {
    position: absolute;
    left: 236px;
    top: 222px;
    width: 729px;
    height: 718px;
    background: var(--label-black);
    overflow: hidden;
  }
  .label__pattern {
    position: absolute;
    inset: 0;
    background:
      radial-gradient(ellipse at 50% 50%, var(--pattern-gold) 0%, #2a1f12 45%, var(--pattern-dark) 85%, var(--label-black) 100%);
  }
  .label__panel {
    position: absolute;
    left: 118px;
    top: 168px;
    width: 492px;
    height: 384px;
    background: radial-gradient(ellipse at 50% 45%, var(--panel-center) 0%, #101010 45%, var(--panel-edge) 100%);
  }
  .label__name {
    position: absolute;
    left: 0;
    right: 0;
    margin: 0;
    font-family: "Great Vibes", cursive;
    font-weight: 400;
    color: var(--gold);
    text-align: center;
    line-height: 1;
    white-space: nowrap;
  }
  .label__name--brand {
    top: 68px;
    font-size: 104px;
  }
  .label__name--type {
    top: 196px;
    font-size: 84px;
    padding-left: 30px;
  }
</style>
</head>
<body>
  <main class="canvas">
    <section class="label">
      <div class="label__pattern" role="img" aria-label="Gold art deco pattern of nested diamond lines on black"></div>
      <div class="label__panel">
        <h1 class="label__name label__name--brand">Corvessa</h1>
        <p class="label__name label__name--type">Wines</p>
      </div>
    </section>
  </main>
</body>
</html>
```